Album Cover Art for New Single

Independent singer-songwriter and pianist, seeking design work for a new single "Walk Beside the Lantern". Christian & Gospel music format. See attached for master recording.

This single is personal for me, so I'm looking for an image that really captures the heart of the message. Redemption, forgiveness, prodigals returning home to a loving father.
Updates

Target Market(s)

Millenials

Colors

Designer to choose colors to be used in the design.

Requirements
Must have
• simple graphic, must include the following text:
• Walk Beside the Lantern
• Dale Verrick
Should not have
• Avoid "cheesy" look and feel.

```html
<!DOCTYPE html>
<html lang="en">
<head>
<meta charset="utf-8">
<title>Walk Beside the Lantern — Dale Verrick</title>
<link rel="stylesheet" href="https://fonts.googleapis.com/css2?family=Montserrat:wght@400&family=Cormorant+Garamond:wght@500&display=swap">
<style>
  :root {
    --sky: #dfe1e2;
    --mist: #c8cacb;
    --rock: #6b6868;
    --rock-deep: #4a4747;
    --forest: #1c1d1d;
    --ink: #0d0d0d;
    --paper: #ffffff;
  }
  html, body {
    margin: 0;
    padding: 0;
    width: 1200px;
    height: 1200px;
    overflow: hidden;
    background: var(--sky);
  }
  .cover {
    position: relative;
    width: 1200px;
    height: 1200px;
    overflow: hidden;
  }
  .cover-backdrop {
    position: absolute;
    inset: 0;
    width: 1200px;
    height: 1200px;
  }
  .title {
    position: absolute;
    left: 58px;
    top: 0;
    margin: 0;
    font-family: "Montserrat", sans-serif;
    font-weight: 400;
    font-size: 210px;
    letter-spacing: -3px;
    line-height: 1;
  }
  .title-line {
    position: absolute;
    left: 0;
    white-space: nowrap;
    color: var(--paper);
  }
  .title-line--first { top: 30px; color: var(--ink); }
  .title-line--second { top: 317px; }
  .title-line--third { top: 604px; }
  .title-line--fourth { top: 891px; }
  .artist {
    position: absolute;
    left: 626px;
    top: 728px;
    margin: 0;
    font-family: "Cormorant Garamond", serif;
    font-weight: 500;
    font-size: 30px;
    letter-spacing: 7px;
    color: var(--paper);
    text-transform: uppercase;
    white-space: nowrap;
  }
</style>
</head>
<body>
  <main class="cover">
    <svg class="cover-backdrop" viewBox="0 0 1200 1200" role="img" aria-label="Photograph of a snow-covered mountain peak wrapped in low mist, with a dark pine forest along the bottom edge">
      <defs>
        <linearGradient id="landscape-tone" x1="0" y1="0" x2="0" y2="1">
          <stop offset="0" stop-color="var(--sky)"/>
          <stop offset="0.18" stop-color="#cfd1d2"/>
          <stop offset="0.35" stop-color="#8f8c8c"/>
          <stop offset="0.55" stop-color="var(--rock)"/>
          <stop offset="0.72" stop-color="var(--mist)"/>
          <stop offset="0.84" stop-color="#8a8b8b"/>
          <stop offset="1" stop-color="var(--forest)"/>
        </linearGradient>
      </defs>
      <rect width="1200" height="1200" fill="url(#landscape-tone)"/>
    </svg>

    <h1 class="title" aria-label="Walk Beside the Lantern">
      <span class="title-line title-line--first">WALK</span>
      <span class="title-line title-line--second">BESIDE</span>
      <span class="title-line title-line--third">THE</span>
      <span class="title-line title-line--fourth">LANTERN</span>
    </h1>

    <p class="artist">Dale Verrick</p>
  </main>
</body>
</html>
```